Vardem Web, LLC. is the name of the company that will be an Internet startup working in E-commerce and

We are a new company and going to start the business by hiring people we need. We are on “Hiring Now…” status right now which we like to be displayed on the website homepage.
The website should allow us to start the hiring process with letting people see and apply for jobs posted on the website.

the company logo is attached.

Target Market(s)

Tech Job Seekers, Programmers, iOS and Android Developers, Software engineers, Graphic designers, QA engineers, Customer Service Reps,...

Industry/Entity Type

Internet

Number of Pages Required

5+ page

Font styles to use
Serif
Sans Serif

Colors

Designer to choose colors to be used in the design.

Requirements
Must have
• We need a system to help job seekers to upload the resume and cover letter and fill the required forms and answer some questions on a form designed to evaluate the job seekers and let them know if they fit in the position and should apply for it.
• We also want job seekers to do a Pre-Employment Tests including Aptitude, Personality, and Skills after they qualified for a job which links our website to web-based pre-employment testing services websites like (Talvexa, Plivmark, Quorvane & Associates, Dunholt Assessment, …)

```html
<!DOCTYPE html>
<html lang="en">
<head>
<meta charset="utf-8">
<title>Vardem Web – Hiring Now</title>
<link rel="stylesheet" href="https://fonts.googleapis.com/css2?family=Lato:wght@400;700;900&display=swap">
<style>
:root{
  --teal:#3aa6d4;
  --teal-dark:#2a8fbd;
  --orange:#f15a22;
  --ink:#3a3a3a;
  --muted:#6b6b6b;
  --dark:#1f2022;
  --darker:#111214;
  --mint:#bfe3e6;
  --white:#ffffff;
}
*{margin:0;padding:0;box-sizing:border-box}
html,body{width:1200px;height:4147px;overflow:hidden}
body{font-family:"Lato",Arial,sans-serif;color:var(--ink);background:var(--white);position:relative}
.abs{position:absolute}
.btn{position:absolute;display:flex;align-items:center;background:var(--orange);color:var(--white);border-radius:40px;font-weight:700;text-transform:uppercase;padding-left:34px}
.btn .dot{position:absolute;right:10px;top:50%;transform:translateY(-50%);border-radius:50%;background:var(--white)}
.heading{position:absolute;font-weight:700;color:var(--teal);text-align:center}
.heading .accent{color:var(--orange)}
.mark{position:absolute;width:18px;height:18px;border-radius:50%;border:3px solid var(--teal)}
.lorem{font-size:15px;line-height:1.65;color:var(--muted)}

/* nav */
.nav{left:0;top:0;width:1200px;height:55px;background:rgba(58,166,212,.85);z-index:3}
.nav a{position:absolute;top:0;height:55px;line-height:55px;color:var(--white);font-size:17px;text-decoration:none;text-transform:uppercase}
.nav a.active{border-bottom:3px solid var(--white);opacity:1}
.brand-box{left:487px;top:0;width:226px;height:116px;background:var(--white);z-index:4;display:flex;align-items:center;justify-content:center;gap:10px}
.brand-box span{font-size:36px;font-weight:900;color:var(--teal);letter-spacing:1px}
.brand-box i{width:22px;height:22px;border-radius:50%;background:var(--orange);display:block}

/* hero */
.hero{left:0;top:0;width:1200px;height:683px;background:linear-gradient(100deg,#e9e4dc 0%,#d9cfc3 45%,#b8a28e 75%,#8c7462 100%)}
.hero-name{left:77px;top:210px;font-size:100px;font-weight:900;color:var(--teal);line-height:1}
.hero-title{left:77px;top:355px;font-size:62px;font-weight:700;color:var(--teal);letter-spacing:1px}
.hero-title .accent{color:var(--orange)}

/* about */
.about-title{left:77px;top:728px;font-size:38px;text-align:left}
.about-text{left:77px;top:812px;width:490px}
.divider{left:603px;top:730px;width:3px;height:370px;background:#e2e2e2}
.video{left:650px;top:830px;width:437px;height:281px;background:linear-gradient(135deg,#6d7e86,#3f4b52)}
.play{left:838px;top:940px;width:62px;height:62px;border:4px solid var(--white);border-radius:50%}

/* process */
.process{left:0;top:1183px;width:1200px;height:545px;background:linear-gradient(180deg,#2c2d30,#202124)}
.process-title{left:0;top:1218px;width:1200px;font-size:40px}
.step-num{width:34px;height:34px;border-radius:50%;background:var(--teal);color:var(--white);font-weight:700;font-size:19px;display:flex;align-items:center;justify-content:center}
.step{color:var(--white);font-size:14px;line-height:1.45;width:130px}
.step h3{color:var(--teal);font-size:20px;font-weight:400;margin-bottom:6px}
.step .more{color:var(--orange);text-decoration:underline;font-size:13px}
.ring{border-radius:50%;background:var(--white);border:12px solid var(--teal)}
.ring svg{position:absolute;left:50%;top:50%;transform:translate(-50%,-50%)}

/* career */
.career-title{left:80px;top:1762px;font-size:38px;text-align:left}
.career-list{left:83px;top:1842px;list-style:none;font-size:19px;line-height:30px;color:var(--ink)}
.career-list li{display:flex;align-items:center;gap:14px}
.career-list li::before{content:"";width:12px;height:12px;border:2px solid var(--teal);border-radius:50%}
.career-photo{left:567px;top:1728px;width:633px;height:360px;background:linear-gradient(120deg,#5a4a3e,#8a7363 55%,#3f342d)}
.tablet{left:740px;top:1785px;width:320px;height:230px;background:var(--white);border:14px solid #1b1b1b;border-radius:14px;display:flex;flex-direction:column;align-items:center;justify-content:center;transform:rotate(-8deg)}
.tablet b{font-size:40px;color:var(--teal);font-weight:900}
.tablet p{color:var(--teal);font-size:19px;text-align:center;line-height:1.3;margin-top:6px}

/* banner */
.banner{left:0;top:2088px;width:1200px;height:420px;background:var(--mint)}
.banner-mark{left:565px;top:2165px;width:70px;height:70px;border-radius:50%;background:var(--teal)}
.banner-text{left:170px;top:2268px;width:860px;text-align:center;font-size:17px;line-height:1.55;color:#4e6b70}

/* services */
.services-title{left:0;top:2555px;width:1200px;font-size:38px}
.svc-icon{width:62px;height:62px;border-radius:50%;background:var(--teal);border:5px solid var(--white)}
.svc-img{height:167px}
.svc-name{font-size:17px;color:var(--teal);text-align:center;width:249px}
.svc-text{font-size:14px;line-height:1.55;color:var(--muted);text-align:center;width:249px}

/* blog */
.blog-title{left:0;top:3275px;width:1200px;font-size:38px}
.blog-img{width:332px;height:271px}
.date{width:94px;height:92px;background:var(--orange);color:var(--white);text-align:center;padding-top:8px}
.date b{display:block;font-size:38px;line-height:1}
.date span{font-size:15px}
.blog-text{font-size:15px;line-height:1.6;color:var(--ink);width:225px}

/* footer */
.footer{left:0;top:3741px;width:1200px;height:337px;background:var(--dark)}
.foot-brand{left:110px;top:3815px;display:flex;align-items:center;gap:12px}
.foot-brand span{font-size:48px;font-weight:900;color:var(--teal)}
.foot-brand i{width:26px;height:26px;border-radius:50%;background:var(--orange)}
.foot-text{left:110px;top:3910px;width:230px;font-size:15px;line-height:1.5;color:var(--white)}
.social{width:46px;height:46px;border:2px solid var(--white);border-radius:50%}
.foot-h{font-size:16px;color:var(--orange);font-weight:700;text-transform:uppercase}
.foot-list{list-style:none;font-size:15px;color:var(--white);line-height:28px}
.foot-list li{display:flex;align-items:center;gap:12px}
.foot-list li::before{content:"";width:10px;height:10px;border:2px solid var(--teal);border-radius:50%}
.contact-row{display:flex;gap:14px;font-size:14px;color:var(--white);line-height:1.5}
.news-text{font-size:14px;line-height:1.6;color:var(--white);width:250px}
.news-input{width:249px;height:44px;background:var(--white);font-size:13px;color:#888;padding:13px 10px}
.copyright{left:0;top:4078px;width:1200px;height:69px;background:var(--darker);color:var(--white);font-size:14px;text-align:center;line-height:69px;border-top:1px solid #333}
</style>
</head>
<body>

<!-- Hero -->
<div class="abs hero" role="img" aria-label="Photo of a woman reading a document at a laptop in a bright office"></div>
<nav class="abs nav">
  <a class="active" style="left:148px">Home</a>
  <a style="left:250px">About</a>
  <a style="left:358px">Services</a>
  <a style="left:765px">Career</a>
  <a style="left:885px">News</a>
  <a style="left:985px">Contact</a>
</nav>
<div class="abs brand-box"><span>VARDEM</span><i></i></div>

<div class="abs hero-name">VARDEM</div>
<div class="abs hero-title">HIRING <span class="accent">NOW...</span></div>
<a class="btn" style="left:77px;top:456px;width:346px;height:69px;font-size:20px">Get started with us<span class="dot" style="width:46px;height:46px"></span></a>

<!-- About -->
<h2 class="heading about-title">About <span class="accent">Vardem</span></h2>
<span class="mark" style="left:176px;top:780px"></span>
<p class="abs lorem about-text">Lorem Ipsum is simply dummy text of the printing and typesetting industry. Lorem Ipsum has been the industry's standard dummy text ever since the 1500s, when an unknown printer took a galley of type and scrambled it to make a type specimen book. It has survived not only five centuries, but also the leap into electronic typesetting, remaining essentially unchanged. It was popularised in the 1960s with the release of Letraset sheets containing Lorem Ipsum passages, and more recently with desktop publishing software like Aldus PageMaker including versions of Lorem Ipsum.</p>
<a class="btn" style="left:77px;top:1052px;width:218px;height:56px;font-size:18px">Read more<span class="dot" style="width:38px;height:38px"></span></a>
<div class="abs divider"></div>
<h2 class="heading" style="left:650px;top:728px;font-size:38px;text-align:left">Candidate Say About <span class="accent">Vardem</span></h2>
<span class="mark" style="left:858px;top:780px"></span>
<div class="abs video" role="img" aria-label="Video still of a smiling candidate at a desk"></div>
<div class="abs play"><svg width="54" height="54" viewBox="0 0 54 54"><polygon points="21,15 21,39 39,27" fill="#fff"/></svg></div>

<!-- Process -->
<div class="abs process" role="img" aria-label="Dark background with faint photos of candidates"></div>
<h2 class="heading process-title">HOW TO <span class="accent">PROCESS....!</span></h2>

<div class="abs ring" style="left:437px;top:1336px;width:138px;height:138px"><svg width="50" height="50" viewBox="0 0 50 50" fill="none" stroke="#333" stroke-width="2.5"><rect x="10" y="6" width="24" height="32" rx="2"/><circle cx="34" cy="34" r="8"/></svg></div>
<div class="abs ring" style="left:642px;top:1336px;width:138px;height:138px"><svg width="50" height="50" viewBox="0 0 50 50" fill="none" stroke="#333" stroke-width="2.5"><circle cx="25" cy="22" r="14"/><path d="M18 36v8h12v-8"/></svg></div>
<div class="abs ring" style="left:282px;top:1502px;width:138px;height:138px"><svg width="50" height="50" viewBox="0 0 50 50" fill="none" stroke="#333" stroke-width="2.5"><circle cx="25" cy="22" r="14"/><circle cx="25" cy="22" r="5"/></svg></div>
<div class="abs ring" style="left:794px;top:1502px;width:138px;height:138px"><svg width="50" height="50" viewBox="0 0 50 50" fill="none" stroke="#333" stroke-width="2.5"><rect x="12" y="6" width="26" height="36" rx="2"/><polyline points="18,26 23,31 32,20"/></svg></div>
<div class="abs ring" style="left:440px;top:1493px;width:276px;height:276px;background:linear-gradient(160deg,#e8eef2,#8ea9bd)" role="img" aria-label="Photo of a man working at a computer in an office"></div>
<div class="abs" style="left:0;top:1728px;width:1200px;height:60px;background:var(--white)"></div>

<div class="abs step-num" style="left:210px;top:1324px">2</div>
<div class="abs step" style="left:254px;top:1322px"><h3>Personality</h3>Lorem Ipsum type simply dummy text of the printing and typesetting industry.<br><span class="more">READ MORE</span></div>
<div class="abs step-num" style="left:790px;top:1324px">3</div>
<div class="abs step" style="left:835px;top:1322px"><h3>Skills</h3>Lorem Ipsum type simply dummy text of the printing and typesetting industry.<br><span class="more">READ MORE</span></div>
<div class="abs step-num" style="left:77px;top:1457px">1</div>
<div class="abs step" style="left:119px;top:1502px"><h3>Aptitude Test</h3>Lorem Ipsum type simply dummy text of the printing and typesetting industry.<br><span class="more">READ MORE</span></div>
<div class="abs step-num" style="left:948px;top:1504px">4</div>
<div class="abs step" style="left:993px;top:1502px"><h3>Qualified</h3>Lorem Ipsum type simply dummy text of the printing and typesetting industry.<br><span class="more">READ MORE</span></div>

<!-- Career -->
<h2 class="heading career-title">CHOOSE YOUR CAREER.!</h2>
<span class="mark" style="left:305px;top:1812px"></span>
<ul class="abs career-list">
  <li>Tech Job Seekers</li>
  <li>Programmers</li>
  <li>iOS and Android Developers</li>
  <li>Software engineers</li>
  <li>Graphic designers</li>
  <li>QA engineers</li>
  <li>Customer Service Reps</li>
</ul>
<div class="abs career-photo" role="img" aria-label="Photo of hands holding a tablet on a wooden table"></div>
<div class="abs tablet"><b>VARDEM</b><p>LOOKING JOB HERE<br>World Best way is Here</p></div>

<!-- Banner -->
<div class="abs banner" role="img" aria-label="Pale teal background with faint figures of people among gears"></div>
<div class="abs banner-mark"></div>
<p class="abs banner-text">Lorem Ipsum is simply dummy text of the printing and typesetting industry. Lorem Ipsum has been the industry's standard dummy text ever since the 1500s, when an unknown printer took a galley of type and scrambled it to make a type specimen book. It has survived not only five centuries, but also the leap into electronic typesetting, remaining essentially unchanged.</p>
<a class="btn" style="left:465px;top:2395px;width:268px;height:55px;font-size:18px">Choose option<span class="dot" style="width:36px;height:36px"></span></a>

<!-- Services -->
<h2 class="heading services-title">OUR <span class="accent">SERVICES</span></h2>
<span class="mark" style="left:591px;top:2610px"></span>

<div class="abs svc-icon" style="left:170px;top:2672px"></div>
<div class="abs svc-icon" style="left:430px;top:2672px"></div>
<div class="abs svc-icon" style="left:700px;top:2672px"></div>
<div class="abs svc-icon" style="left:964px;top:2672px"></div>

<div class="abs svc-img" style="left:77px;top:2723px;width:249px;background:linear-gradient(135deg,#2f4a57,#7a8e96)" role="img" aria-label="Photo of a developer typing code at a laptop"></div>
<div class="abs svc-img" style="left:343px;top:2723px;width:249px;background:linear-gradient(135deg,#c9c3bd,#6c5a50)" role="img" aria-label="Photo of a smiling web designer at a desk"></div>
<div class="abs svc-img" style="left:606px;top:2723px;width:248px;background:linear-gradient(135deg,#d8d2c8,#5d6770)" role="img" aria-label="Photo of a software team meeting around a table"></div>
<div class="abs svc-img" style="left:871px;top:2723px;width:252px;background:linear-gradient(135deg,#b8b2a8,#3f4246)" role="img" aria-label="Photo of a customer service agent with a headset"></div>

<div class="abs svc-name" style="left:77px;top:2910px">Ios and Android Development</div>
<div class="abs svc-name" style="left:343px;top:2910px">Web design</div>
<div class="abs svc-name" style="left:606px;top:2910px">Software Development</div>
<div class="abs svc-name" style="left:871px;top:2910px">Custom Servicet</div>

<p class="abs svc-text" style="left:77px;top:2952px">Lorem Ipsum is simply dummy text of the printing and typesetting industry. Lorem Ipsum has been the industry's standard dummy text ever since the 1500s.</p>
<p class="abs svc-text" style="left:343px;top:2952px">Lorem Ipsum is simply dummy text of the printing and typesetting industry. Lorem Ipsum has been the industry's standard dummy text ever since the 1500s.</p>
<p class="abs svc-text" style="left:606px;top:2952px">Lorem Ipsum is simply dummy text of the printing and typesetting industry. Lorem Ipsum has been the industry's standard dummy text ever since the 1500s.</p>
<p class="abs svc-text" style="left:871px;top:2952px">Lorem Ipsum is simply dummy text of the printing and typesetting industry. Lorem Ipsum has been the industry's standard dummy text ever since the 1500s.</p>

<a class="btn" style="left:100px;top:3097px;width:210px;height:56px;font-size:18px">Read more<span class="dot" style="width:38px;height:38px"></span></a>
<a class="btn" style="left:366px;top:3097px;width:210px;height:56px;font-size:18px">Read more<span class="dot" style="width:38px;height:38px"></span></a>
<a class="btn" style="left:629px;top:3097px;width:210px;height:56px;font-size:18px">Read more<span class="dot" style="width:38px;height:38px"></span></a>
<a class="btn" style="left:896px;top:3097px;width:210px;height:56px;font-size:18px">Read more<span class="dot" style="width:38px;height:38px"></span></a>

<!-- Blog -->
<h2 class="heading blog-title">LATEST <span class="accent">BLOG</span></h2>
<span class="mark" style="left:591px;top:3330px"></span>

<div class="abs blog-img" style="left:77px;top:3393px;background:linear-gradient(135deg,#c7b48a,#4d4a45)" role="img" aria-label="Photo of an engineer in a hard hat at work"></div>
<div class="abs blog-img" style="left:434px;top:3393px;background:linear-gradient(180deg,#dfe6ea,#9fb0bb 60%,#4b5a63)" role="img" aria-label="Photo of a person with a telescope above a city skyline"></div>
<div class="abs blog-img" style="left:791px;top:3393px;background:linear-gradient(135deg,#e2e4e2,#6d7a80)" role="img" aria-label="Photo of two colleagues working at laptops"></div>

<div class="abs date" style="left:77px;top:3572px"><b>28</b><span>August</span></div>
<div class="abs date" style="left:434px;top:3572px"><b>29</b><span>August</span></div>
<div class="abs date" style="left:791px;top:3572px"><b>30</b><span>August</span></div>
<p class="abs blog-text" style="left:186px;top:3590px">Lorem Ipsum is simply dummy text of the printing and typesetting industry.</p>
<p class="abs blog-text" style="left:543px;top:3590px">Lorem Ipsum is simply dummy text of the printing and typesetting industry.</p>
<p class="abs blog-text" style="left:900px;top:3590px">Lorem Ipsum is simply dummy text of the printing and typesetting industry.</p>

<!-- Footer -->
<footer class="abs footer"></footer>
<div class="abs foot-brand"><span>VARDEM</span><i></i></div>
<p class="abs foot-text">Lorem Ipsum is simply dummy text of the Printing and type.</p>
<div class="abs social" style="left:112px;top:3987px" aria-label="Social profile"></div>
<div class="abs social" style="left:174px;top:3987px" aria-label="Social profile"></div>
<div class="abs social" style="left:236px;top:3987px" aria-label="Social profile"></div>

<div class="abs foot-h" style="left:406px;top:3800px">Contact us</div>
<ul class="abs foot-list" style="left:406px;top:3836px">
  <li>Home</li><li>About</li><li>Services</li><li>Career</li><li>News</li><li>Contact</li>
</ul>

<div class="abs foot-h" style="left:619px;top:3800px">Contact us</div>
<div class="abs" style="left:619px;top:3836px;display:flex;flex-direction:column;gap:14px">
  <div class="contact-row"><svg width="18" height="22" viewBox="0 0 18 22"><path d="M9 1a7 7 0 0 0-7 7c0 5 7 13 7 13s7-8 7-13a7 7 0 0 0-7-7z" fill="#f15a22"/><circle cx="9" cy="8" r="2.5" fill="#1f2022"/></svg><div><b style="color:var(--orange)">VARDEM WEB</b><br>123 Building Name, Street, City,<br>Country - Zip code</div></div>
  <div class="contact-row"><svg width="18" height="18" viewBox="0 0 18 18"><path d="M4 1l3 4-2 2c1 2 3 4 5 5l2-2 4 3-2 3C8 16 2 10 1 4z" fill="#f15a22"/></svg>555.014.2290</div>
  <div class="contact-row"><svg width="18" height="14" viewBox="0 0 18 14"><rect x="1" y="1" width="16" height="12" fill="#f15a22"/><polyline points="1,1 9,8 17,1" fill="none" stroke="#1f2022" stroke-width="1.5"/></svg>info@vardemweb.com</div>
  <div class="contact-row"><svg width="18" height="18" viewBox="0 0 18 18"><circle cx="9" cy="9" r="8" fill="#f15a22"/></svg>www.vardemweb.com</div>
</div>

<div class="abs foot-h" style="left:874px;top:3800px">Newsletter</div>
<p class="abs news-text" style="left:874px;top:3836px">Would you like to receive exclusive access to articles, white papers and our regular monthly newsletter?</p>
<div class="abs news-input" style="left:874px;top:3940px">Enter Email Id</div>
<a class="btn" style="left:874px;top:3995px;width:166px;height:47px;font-size:16px;padding-left:26px">Subscribe</a>

<div class="abs copyright">VARDEM WEB | Copyright 2017. All Rights Reserved</div>

</body>
</html>
```